Wordpress Design for a Private Label BBQ Brand

For our new brand, we'd need a new Wordpress website. We'd prefer to run the website on Wordpress

We'd like to include the following
- space for description of the brand
- space for product portfolio (not a shop!)
- space for socials
- space for support
- space for contact

```html
<!DOCTYPE html>
<html lang="en">
<head>
<meta charset="utf-8">
<title>Emberly — BBQ</title>
<link rel="stylesheet" href="https://fonts.googleapis.com/css2?family=Crimson+Pro:wght@600;700&family=Inter:wght@400;500&display=swap">
<style>
:root{
  --red:#c41a1f;
  --red-dark:#a3121a;
  --orange:#f0652a;
  --ink:#111111;
  --text:#3a3a3a;
  --muted:#7a7a7a;
  --soft:#f5f5f5;
  --white:#ffffff;
  --grad:linear-gradient(90deg,var(--red) 0%,var(--orange) 100%);
  --serif:"Crimson Pro",Georgia,serif;
  --sans:"Inter",Arial,sans-serif;
}
*{box-sizing:border-box;margin:0;padding:0}
html,body{width:1200px;height:3713px;overflow:hidden}
body{font-family:var(--sans);color:var(--text);background:var(--white);position:relative}
section,header,footer{position:absolute;left:0;width:1200px}
.abs{position:absolute}
.heading{font-family:var(--serif);font-weight:700;color:var(--ink);text-transform:uppercase;letter-spacing:1px;font-size:36px;display:flex;align-items:center;gap:14px;white-space:nowrap}
.heading .dot{width:18px;height:18px;border-radius:50%;background:var(--grad);display:inline-block}
.pill{border-radius:30px;font-family:var(--serif);font-weight:700;font-size:14px;text-transform:uppercase;display:flex;align-items:center;justify-content:center;letter-spacing:.3px}

/* header */
.site-header{top:0;height:131px;background:var(--white);border-top:5px solid var(--red);box-shadow:0 2px 6px rgba(0,0,0,.05)}
.topbar{left:497px;top:0;width:562px;height:50px;background:var(--grad);border-radius:0 0 14px 14px;display:flex;align-items:center;gap:34px;padding-left:58px;color:var(--white);font-size:15px;white-space:nowrap}
.topbar span{display:flex;align-items:center;gap:8px}
.topbar .contact-btn{border:2px solid var(--white);border-radius:18px;padding:5px 24px;font-family:var(--serif);font-size:15px}
.brand-mark{left:112px;top:40px;width:46px;height:46px;border-radius:50%;background:var(--grad)}
.brand{left:168px;top:42px;font-family:var(--serif);font-weight:700;font-size:46px;color:var(--ink);letter-spacing:1px;line-height:56px}
.nav{top:82px;left:520px;display:flex;gap:50px;font-size:16px;color:var(--ink);white-space:nowrap}

/* hero */
.hero{top:131px;height:556px}
.hero-photo{left:0;top:0;width:609px;height:556px;background:radial-gradient(circle at 45% 45%,#5a3020 0%,#2a1a14 40%,#0d0d0d 80%)}
.hero-panel{left:609px;top:0;width:591px;height:556px;background:radial-gradient(circle at 70% 30%,#f4742e 0%,#e34a22 55%,#c9231e 100%)}
.hero h1{left:727px;top:152px;font-family:var(--serif);font-weight:700;font-size:56px;line-height:60px;color:var(--white);letter-spacing:1px}
.hero p{left:727px;top:280px;width:370px;color:var(--white);font-size:15px;line-height:26px}
.hero .pill{left:723px;top:351px;width:147px;height:52px;background:var(--white);color:var(--red)}

/* about */
.about{top:687px;height:609px}
.about-img1{left:114px;top:69px;width:236px;height:395px;border-radius:6px;background:linear-gradient(160deg,#6b5a2a 0%,#3b3025 50%,#5b2a1a 100%)}
.about-img2{left:363px;top:135px;width:236px;height:395px;border-radius:6px;background:linear-gradient(180deg,#1f2a28 0%,#2a2a2a 55%,#c4511b 85%,#1a1a1a 100%)}
.about-badge{left:321px;top:258px;width:66px;height:66px;border-radius:50%;background:var(--grad)}
.about .heading{left:640px;top:65px}
.about p{left:645px;width:440px;font-size:15px;line-height:25.6px;color:var(--text)}
.about .pill{left:638px;top:457px;width:147px;height:54px;background:var(--grad);color:var(--white)}

/* portfolio */
.portfolio{top:1296px;height:721px;background:var(--soft)}
.portfolio .heading{left:0;width:1200px;justify-content:center;top:58px}
.tile{background:linear-gradient(180deg,#ffffff 0%,#eeeeee 100%);box-shadow:0 2px 10px rgba(0,0,0,.06)}

/* social */
.social{top:2017px;height:537px;background:radial-gradient(ellipse at 60% 75%,#5a2a12 0%,#1a1a1a 45%,#0c0c0c 100%)}
.social .heading{left:0;width:1200px;justify-content:center;top:64px;color:var(--white)}
.card{top:167px;width:215px;height:251px;background:var(--white);border-radius:8px;padding:18px 20px}
.card .who{display:flex;gap:10px;align-items:center}
.avatar{width:38px;height:38px;border-radius:50%;background:linear-gradient(135deg,#d9b49a,#9a6a52)}
.card .name{font-family:var(--serif);font-weight:700;font-size:19px;color:var(--ink);line-height:20px}
.card .ago{font-size:11px;color:var(--muted)}
.stars{color:#f5b400;font-size:14px;letter-spacing:3px;margin:8px 0 6px}
.card p{font-size:11px;line-height:22px;color:var(--text)}
.icons{display:flex;gap:14px;margin-top:10px}
.icons i{width:9px;height:9px;border-radius:50%;background:var(--orange);display:block}

/* faq */
.faq{top:2554px;height:738px}
.faq .heading{left:0;width:1200px;justify-content:center;top:72px;text-transform:none;font-size:37px}
.q{left:206px;width:802px;height:72px;border-radius:36px;background:var(--white);box-shadow:0 3px 14px rgba(0,0,0,.09);display:flex;align-items:center;padding-left:6px}
.q .num{width:58px;height:58px;border-radius:50%;background:radial-gradient(circle,#c81e22,#8c1015);color:var(--white);font-family:var(--serif);font-weight:700;font-size:24px;display:flex;align-items:center;justify-content:center}
.q.open .num{background:var(--grad)}
.q .txt{font-family:var(--serif);font-weight:700;font-size:24px;color:var(--ink);margin-left:26px;flex:1;white-space:nowrap}
.q .sign{color:var(--red);font-size:28px;margin-right:36px;font-weight:300}
.answer{left:300px;top:570px;width:660px;border-left:2px solid var(--red);padding-left:17px;font-size:14.5px;line-height:25.5px;color:var(--muted)}

/* footer */
.site-footer{top:3292px;height:421px;background:radial-gradient(ellipse at 50% 40%,#1c1c1c 0%,#050505 80%);color:var(--white)}
.foot-brand{left:115px;top:180px;font-family:var(--serif);font-weight:700;font-size:42px;letter-spacing:1px}
.foot-mark{left:168px;top:66px;width:84px;height:84px;border-radius:50%;background:var(--grad)}
.foot-social{left:134px;top:244px;display:flex;gap:10px}
.foot-social i{width:30px;height:30px;border-radius:50%;background:var(--white);display:block}
.foot-title{font-family:var(--serif);font-weight:700;font-size:21px}
.field{left:402px;width:249px;height:36px;border-radius:18px;background:var(--white);color:#999;font-size:13px;display:flex;align-items:center;justify-content:center}
.submit{left:402px;top:218px;width:249px;height:36px;border-radius:18px;background:var(--grad);font-size:15px;font-weight:500;display:flex;align-items:center;justify-content:center}
.info{left:712px;font-size:15px;line-height:25px;display:flex;gap:12px;white-space:nowrap}
.info svg{flex:none;margin-top:5px}
.links{left:975px;top:106px;font-size:15px;line-height:30px}
.rule{left:112px;top:323px;width:976px;height:1px;background:#2c2c2c}
.copy{left:0;width:1200px;top:358px;text-align:center;font-size:15px}
</style>
</head>
<body>

<header class="site-header">
  <div class="abs topbar">
    <span><svg width="13" height="13" viewBox="0 0 24 24" fill="#fff"><path d="M6.6 10.8a15 15 0 0 0 6.6 6.6l2.2-2.2a1 1 0 0 1 1-.25 11.4 11.4 0 0 0 3.6.57 1 1 0 0 1 1 1V20a1 1 0 0 1-1 1A17 17 0 0 1 3 4a1 1 0 0 1 1-1h3.5a1 1 0 0 1 1 1c0 1.25.2 2.45.57 3.57a1 1 0 0 1-.25 1z"/></svg>+1 555 014 2270</span>
    <span><svg width="13" height="11" viewBox="0 0 24 18" fill="#fff"><path d="M0 0h24v2L12 10 0 2zM0 4l12 8 12-8v14H0z"/></svg>info@emberly.com</span>
    <span class="contact-btn">CONTACT</span>
  </div>
  <div class="abs brand-mark"></div>
  <div class="abs brand">EMBERLY</div>
  <nav class="abs nav"><span>Home</span><span>About</span><span>Product Portfolio</span><span>Support</span><span>Contact</span></nav>
</header>

<section class="hero">
  <div class="abs hero-photo" role="img" aria-label="Photo of a kettle grill loaded with steak, sausages, ribs and skewers"></div>
  <div class="abs hero-panel" role="img" aria-label="Red and orange flame texture background"></div>
  <h1 class="abs">WELCOME TO<br>EMBERLY</h1>
  <p class="abs">Lorem ipsum dolor sit amet, consectetur adipiscing elit, sed do eiusmod tempor incididunt ut labore</p>
  <div class="abs pill">Get Started</div>
</section>

<section class="about">
  <div class="abs about-img1" role="img" aria-label="Photo of sausages on a grill grate outdoors"></div>
  <div class="abs about-img2" role="img" aria-label="Photo of an open grill with flames"></div>
  <div class="abs about-badge"></div>
  <h2 class="abs heading"><span class="dot"></span>About Emberly</h2>
  <p class="abs" style="top:122px">Lorem ipsum dolor sit amet, consectetur adipiscing elit, sed do eiusmod tempor incididunt ut labore et dolore magna aliqua. Quis ipsum suspendisse ultrices gravida. Risus commodo viverra maecenas accumsan lacus vel facilisis. Lorem ipsum dolor sit amet, consectetur adipiscing elit, sed do eiusmod tempor incididunt ut labore et dolore magna aliqua. Quis ipsum suspendisse ultrices gravida. Risus commodo viverra maecenas accumsan lacus vel facilisis.</p>
  <p class="abs" style="top:353px">Lorem ipsum dolor sit amet, consectetur adipiscing elit, sed do eiusmod tempor incididunt ut labore et dolore magna aliqua. Quis ipsum suspendisse ultrices gravida.</p>
  <div class="abs pill">Learn More</div>
</section>

<section class="portfolio">
  <h2 class="abs heading"><span class="dot"></span>Product Portfolio</h2>
  <div class="abs tile" style="left:109px;top:142px;width:485px;height:243px" role="img" aria-label="Close-up of a ceramic kamado grill base and vent"></div>
  <div class="abs tile" style="left:606px;top:142px;width:238px;height:236px" role="img" aria-label="Small black kamado grill on a stand"></div>
  <div class="abs tile" style="left:853px;top:142px;width:236px;height:236px" role="img" aria-label="Stainless steel grill spatula"></div>
  <div class="abs tile" style="left:109px;top:394px;width:240px;height:236px" role="img" aria-label="Kamado grill lid with top vent"></div>
  <div class="abs tile" style="left:357px;top:394px;width:238px;height:236px" role="img" aria-label="Aluminium grill tool case"></div>
  <div class="abs tile" style="left:604px;top:385px;width:485px;height:245px" role="img" aria-label="Set of grill tools: spatula, tongs, brush, fork and skewers"></div>
</section>

<section class="social" role="img" aria-label="Dark background with a flaming grill">
  <h2 class="abs heading"><span class="dot"></span>Our Social</h2>
  <div class="abs card" style="left:111px">
    <div class="who"><div class="avatar"></div><div><div class="name">Marla Quint</div><div class="ago">1month ago</div></div></div>
    <div class="stars">★★★★★</div>
    <p>Lorem ipsum dolor sit amet, consectetur adipiscing elit, sed do eiusmod tempor incididunt ut labore et dolore magna aliqua. Quis ipsum suspendisse.</p>
    <div class="icons"><i></i><i></i><i></i><i></i></div>
  </div>
  <div class="abs card" style="left:366px">
    <div class="who"><div class="avatar"></div><div><div class="name">Marla Quint</div><div class="ago">1month ago</div></div></div>
    <div class="stars">★★★★★</div>
    <p>Lorem ipsum dolor sit amet, consectetur adipiscing elit, sed do eiusmod tempor incididunt ut labore et dolore magna aliqua. Quis ipsum suspendisse.</p>
    <div class="icons"><i></i><i></i><i></i><i></i></div>
  </div>
  <div class="abs card" style="left:619px">
    <div class="who"><div class="avatar"></div><div><div class="name">Marla Quint</div><div class="ago">1month ago</div></div></div>
    <div class="stars">★★★★★</div>
    <p>Lorem ipsum dolor sit amet, consectetur adipiscing elit, sed do eiusmod tempor incididunt ut labore et dolore magna aliqua. Quis ipsum suspendisse.</p>
    <div class="icons"><i></i><i></i><i></i><i></i></div>
  </div>
  <div class="abs card" style="left:874px">
    <div class="who"><div class="avatar"></div><div><div class="name">Marla Quint</div><div class="ago">1month ago</div></div></div>
    <div class="stars">★★★★★</div>
    <p>Lorem ipsum dolor sit amet, consectetur adipiscing elit, sed do eiusmod tempor incididunt ut labore et dolore magna aliqua. Quis ipsum suspendisse.</p>
    <div class="icons"><i></i><i></i><i></i><i></i></div>
  </div>
</section>

<section class="faq">
  <h2 class="abs heading"><span class="dot"></span>Frequently Asked Questions</h2>
  <div class="abs q" style="top:172px"><span class="num">01</span><span class="txt">Lorem ipsum dolor sit amet, consectetur adipiscing elit</span><span class="sign">+</span></div>
  <div class="abs q" style="top:271px"><span class="num">02</span><span class="txt">Lorem ipsum dolor sit amet, consectetur adipiscing elit</span><span class="sign">+</span></div>
  <div class="abs q" style="top:373px"><span class="num">03</span><span class="txt">Lorem ipsum dolor sit amet, consectetur adipiscing elit</span><span class="sign">+</span></div>
  <div class="abs q open" style="top:477px"><span class="num">04</span><span class="txt">Lorem ipsum dolor sit amet, consectetur adipiscing elit</span><span class="sign">−</span></div>
  <p class="abs answer">Lorem ipsum dolor sit amet, consectetur adipiscing elit, sed do eiusmod tempor incididunt ut labore et dolore magna aliqua. Quis ipsum suspendisse ultrices gravida. Risus commodo viverra maecenas accumsan lacus vel facilisis.</p>
</section>

<footer class="site-footer">
  <div class="abs foot-mark"></div>
  <div class="abs foot-brand">EMBERLY</div>
  <div class="abs foot-social"><i></i><i></i><i></i><i></i></div>

  <div class="abs foot-title" style="left:406px;top:70px">Get A Quote</div>
  <div class="abs field" style="top:113px">First Name</div>
  <div class="abs field" style="top:165px">Last Name</div>
  <div class="abs submit">Submit</div>

  <div class="abs foot-title" style="left:712px;top:64px">Contact Us</div>
  <div class="abs info" style="top:114px"><svg width="12" height="15" viewBox="0 0 12 16" fill="#fff"><path d="M6 0a6 6 0 0 1 6 6c0 4.5-6 10-6 10S0 10.5 0 6a6 6 0 0 1 6-6zm0 3.5A2.5 2.5 0 1 0 6 8.5 2.5 2.5 0 0 0 6 3.5z"/></svg><span>12B Emberly Lorem ipsum<br>dolor sit amet</span></div>
  <div class="abs info" style="top:180px"><svg width="14" height="11" viewBox="0 0 24 18" fill="#fff"><path d="M0 0h24v2L12 10 0 2zM0 4l12 8 12-8v14H0z"/></svg><span>info@emberly.com</span></div>
  <div class="abs info" style="top:213px"><svg width="13" height="13" viewBox="0 0 24 24" fill="#fff"><path d="M6.6 10.8a15 15 0 0 0 6.6 6.6l2.2-2.2a1 1 0 0 1 1-.25 11.4 11.4 0 0 0 3.6.57 1 1 0 0 1 1 1V20a1 1 0 0 1-1 1A17 17 0 0 1 3 4a1 1 0 0 1 1-1h3.5a1 1 0 0 1 1 1c0 1.25.2 2.45.57 3.57a1 1 0 0 1-.25 1z"/></svg><span>Tel.: +1 555 014 2270</span></div>

  <div class="abs foot-title" style="left:971px;top:63px">Quick Link</div>
  <div class="abs links">Home<br>About<br>Product Portfolio<br>Support<br>Contact</div>

  <div class="abs rule"></div>
  <div class="abs copy">©Copyrights 2023 &nbsp;Emberly &nbsp;| &nbsp;&nbsp;All Rights Reserved</div>
</footer>

</body>
</html>
```